Mindfulness School for Children -- Business Cards

We're looking for business cards for our school directors and owners. We're a mindfulness school for children called little lanterns. Attached are our logos/icons.

```html
<!DOCTYPE html>
<html lang="en">
<head>
<meta charset="utf-8">
<title>Little Lanterns — Business Cards</title>
<link href="https://fonts.googleapis.com/css2?family=Arimo:wght@400;700&display=swap" rel="stylesheet">
<style>
  :root {
    --backdrop: #d6d6d6;
    --card: #262626;
    --teal: #5cb8cc;
    --line: #3a8f9c;
    --mint: #86cfa0;
    --text: #f2f2f2;
  }
  * { margin: 0; padding: 0; box-sizing: border-box; }
  html, body { width: 1200px; height: 788px; overflow: hidden; }
  body {
    background: var(--backdrop);
    font-family: "Arimo", Arial, sans-serif;
    position: relative;
  }
  .card {
    position: absolute;
    width: 520px;
    height: 300px;
    background: var(--card);
    border-radius: 26px;
    color: var(--text);
  }
  .card--back { left: 50px; top: 110px; }
  .card--front { left: 630px; top: 378px; }

  .identity {
    position: absolute;
    top: 92px;
    left: 0; right: 0;
    text-align: center;
    white-space: nowrap;
  }
  .identity__name {
    font-weight: 700;
    font-size: 21px;
    letter-spacing: 0.5px;
    background: linear-gradient(90deg, var(--teal), var(--mint));
    -webkit-background-clip: text;
    background-clip: text;
    color: transparent;
  }
  .identity__divider {
    display: inline-block;
    width: 1px; height: 14px;
    background: var(--line);
    margin: 0 8px;
    vertical-align: -1px;
  }
  .identity__role { font-size: 12px; }

  .rule {
    position: absolute;
    left: 34px; right: 34px;
    height: 1px;
    background: var(--line);
  }
  .rule--top { top: 130px; }
  .rule--bottom { top: 166px; }

  .contacts {
    position: absolute;
    top: 140px;
    left: 0; right: 0;
    display: flex;
    justify-content: center;
    gap: 16px;
    font-size: 12px;
    white-space: nowrap;
  }
  .contacts__item { display: flex; align-items: center; gap: 5px; }
  .contacts__icon { width: 10px; height: 10px; fill: var(--teal); }

  .address {
    position: absolute;
    top: 180px;
    left: 0; right: 0;
    text-align: center;
    font-size: 12px;
  }

  .brand {
    position: absolute;
    inset: 0;
    display: flex;
    align-items: center;
    justify-content: center;
    gap: 12px;
  }
  .brand__dot {
    width: 14px; height: 14px;
    border-radius: 50%;
    background: var(--teal);
  }
  .brand__name {
    font-weight: 700;
    font-size: 46px;
    color: var(--teal);
    letter-spacing: 0.5px;
  }
</style>
</head>
<body>
  <section class="card card--back">
    <div class="identity">
      <span class="identity__name">MARA ELLISON</span><span class="identity__divider"></span><span class="identity__role">CEO/Founder</span>
    </div>
    <div class="rule rule--top"></div>
    <div class="contacts">
      <span class="contacts__item">
        <svg class="contacts__icon" viewBox="0 0 10 10" aria-hidden="true"><path d="M2 0.5 L3.6 2.6 L2.7 3.6 Q3.6 5.8 6.4 7.3 L7.4 6.4 L9.5 8 L8.3 9.5 Q3.5 9 0.5 1.7 Z"/></svg>
        (00) 5290 3168
      </span>
      <span class="contacts__item">
        <svg class="contacts__icon" viewBox="0 0 10 10" aria-hidden="true"><path d="M0.5 2 H9.5 V8 H0.5 Z M1 2.5 L5 5.6 L9 2.5" stroke="#262626" stroke-width="0.7"/></svg>
        info@littlelanterns.com
      </span>
      <span class="contacts__item">
        <svg class="contacts__icon" viewBox="0 0 10 10" aria-hidden="true"><circle cx="5" cy="5" r="4.5"/><path d="M0.5 5 H9.5 M5 0.5 Q2.5 5 5 9.5 M5 0.5 Q7.5 5 5 9.5" stroke="#262626" stroke-width="0.6" fill="none"/></svg>
        www.littlelanterns.com
      </span>
    </div>
    <div class="rule rule--bottom"></div>
    <p class="address">Po Box 4120 Elm Road Country Name, AB 60318</p>
  </section>

  <section class="card card--front">
    <div class="brand">
      <span class="brand__dot"></span>
      <span class="brand__name">littlelanterns</span>
    </div>
  </section>
</body>
</html>
```